Quote Cards With KB May 2025 for Instagram

I would like to put these quotes over one of the pictures attached; Instagram (new size: 4:5 (1080 x 1350 pixels) One Quote per picture, and I want the quote to be bold or easy to read as well. I provided a few reference graphics that I really like as examples below. In very small letters at the bottom add @KBHarlowOnline

All of the pictures are attached; you can pick any photo and add one quote to it; but no stock photography

```html
<!DOCTYPE html>
<html lang="en">
<head>
<meta charset="utf-8">
<title>Quote Card – Hormones</title>
<link href="https://fonts.googleapis.com/css2?family=Nunito+Sans:wght@500;800;900&display=swap" rel="stylesheet">
<style>
  :root {
    --panel-dark: #2a2226;
    --panel-plum: #5a1a3c;
    --panel-magenta: #c9006b;
    --text-light: #ffffff;
    --room-warm: #6e5a52;
    --room-shadow: #3a302e;
    --window-night: #101a3c;
    --city-blue: #2a55b8;
    --city-glow: #4d7fe0;
    --floor-wood: #c4a88c;
    --floor-light: #dcc6ae;
  }
  html, body {
    margin: 0;
    padding: 0;
    width: 960px;
    height: 1200px;
    overflow: hidden;
    background: var(--panel-dark);
  }
  .quote-card {
    position: relative;
    width: 960px;
    height: 1200px;
    display: flex;
    font-family: "Nunito Sans", sans-serif;
  }
  .portrait {
    width: 487px;
    height: 1200px;
    background:
      radial-gradient(ellipse 190px 360px at 400px 500px, rgba(77,127,224,0.55), rgba(77,127,224,0) 100%),
      radial-gradient(ellipse 160px 220px at 70px 640px, rgba(77,127,224,0.35), rgba(77,127,224,0) 100%),
      radial-gradient(ellipse 260px 180px at 120px 160px, rgba(110,90,82,0.9), rgba(110,90,82,0) 100%),
      radial-gradient(ellipse 320px 160px at 240px 1150px, rgba(220,198,174,0.7), rgba(220,198,174,0) 100%),
      linear-gradient(90deg,
        rgba(58,48,46,0.0) 0%,
        rgba(26,22,26,0.35) 40%,
        rgba(26,22,26,0.35) 60%,
        rgba(58,48,46,0.0) 100%),
      linear-gradient(180deg,
        var(--room-warm) 0%,
        var(--room-shadow) 14%,
        var(--window-night) 28%,
        var(--city-blue) 52%,
        var(--window-night) 72%,
        var(--room-shadow) 77%,
        var(--floor-wood) 84%,
        var(--floor-light) 100%);
  }
  .quote-panel {
    position: relative;
    flex: 1;
    height: 1200px;
    background: linear-gradient(180deg,
      var(--panel-dark) 0%,
      var(--panel-plum) 22%,
      var(--panel-magenta) 50%,
      var(--panel-plum) 80%,
      var(--panel-dark) 100%);
    color: var(--text-light);
  }
  .quote {
    position: absolute;
    top: 184px;
    left: 0;
    right: 0;
    margin: 0;
    text-align: center;
    font-weight: 800;
    font-size: 58px;
    line-height: 75.5px;
    letter-spacing: -0.5px;
    text-transform: uppercase;
  }
  .quote span { display: block; }
  .handle {
    position: absolute;
    top: 1104px;
    left: 0;
    right: 0;
    text-align: center;
    font-weight: 900;
    font-size: 15px;
    letter-spacing: 0;
  }
  .card-code {
    position: absolute;
    right: 24px;
    top: 1163px;
    font-weight: 500;
    font-size: 15px;
    opacity: 0.85;
  }
</style>
</head>
<body>
  <main class="quote-card">
    <div class="portrait" role="img" aria-label="Photo of KB standing in a sheer black top and black jeans beside a window overlooking a city at night"></div>
    <section class="quote-panel">
      <p class="quote">
        <span>Tired.</span>
        <span>Moody.</span>
        <span>Stubborn</span>
        <span>Belly fat.</span>
        <span>Your</span>
        <span>Hormones</span>
        <span>are</span>
        <span>screaming</span>
        <span>for help!</span>
        <span>Let’s fix</span>
        <span>that.</span>
      </p>
      <div class="handle">@KBHARLOWONLINE</div>
      <div class="card-code">C 25</div>
    </section>
  </main>
</body>
</html>
```